We are a local Communty Pharmacy wishing to promote and market a specialised Pharmaceutical Service

We would like a design that is professional and enticing ( according to the brief In attached files)
We wish to Market Compounding Pharmacy as a specialist side of our business.
We have the expertise a purpose built preparation laboratory.
The main purpose is an Internet presence that entices prospective patients to contact or visit our physical store.

Target Market(s)

Patients Medicos and Veterinary clients

Industry/Entity Type

Pharmacy

Coding

Coded - Design and coding required

Number of Pages Required

1 page

Requirements
Must have
• Clear friendly image
Nice to have
• soft enticing feel
Should not have
• No crass loud unprofessional elements

```html
<!DOCTYPE html>
<html lang="en">
<head>
<meta charset="utf-8">
<title>Compounding Pharmacy</title>
<link href="https://fonts.googleapis.com/css2?family=Lato:wght@300;400;700;900&display=swap" rel="stylesheet">
<style>
:root{
  --lime:#8cc63f;
  --lime-dark:#76ad2e;
  --teal:#2d5561;
  --teal-soft:rgba(88,168,180,.78);
  --ink:#33393f;
  --muted:#8a9198;
  --line:#e3e6e9;
  --band:#2e3a45;
  --band-dark:#25303a;
  --foot:#eef0f2;
  --bottom:#23292f;
  --white:#ffffff;
}
*{box-sizing:border-box;margin:0;padding:0}
html,body{width:1200px;height:2400px;overflow:hidden}
body{font-family:'Lato',sans-serif;color:var(--ink);background:var(--white);position:relative}
.wrap{width:832px;margin:0 auto;position:relative}

.topbar{height:24px;background:#2b2f33;border-top:3px solid var(--lime);color:#c9ced3;font-size:10px}
.topbar .wrap{display:flex;justify-content:space-between;align-items:center;height:21px}
.topbar .left{display:flex;gap:40px}
.topbar .right{display:flex;gap:6px}
.topbar .sq{width:10px;height:10px;background:#5b636b;border-radius:2px}
.select{display:inline-block;padding:0 18px 0 4px;background:#3a4046;border-radius:2px}

.header{height:80px}
.header .wrap{display:flex;justify-content:space-between;align-items:center;height:80px}
.logo{font-size:24px;font-weight:700;color:var(--teal);letter-spacing:.5px}
.nav{display:flex;gap:26px;font-size:12px;color:#555c63}
.nav a{color:inherit;text-decoration:none}

.hero{position:relative;height:504px;background:linear-gradient(90deg,#d7e3e9 0%,#eef2f4 30%,#f7f8f8 45%,#e4ecef 70%,#cfdde4 100%)}
.hero-title{position:absolute;left:164px;top:262px;width:300px;height:48px;background:var(--teal-soft);color:var(--white);font-size:26px;font-weight:300;display:flex;align-items:center;justify-content:center}
.hero-sub{position:absolute;left:340px;top:330px;width:110px;height:14px;background:var(--lime);color:var(--white);font-size:8px;text-align:center;line-height:14px}
.hero-btn{position:absolute;left:332px;top:446px;width:120px;height:36px;background:var(--band);color:var(--white);font-size:10px;font-weight:700;display:flex;align-items:center;justify-content:center;letter-spacing:.5px}

.welcome{padding-top:30px;height:400px;text-align:center}
.h-center{font-size:22px;font-weight:900;letter-spacing:1px;color:#3a4046}
.welcome .intro{width:1040px;margin:20px auto 0;font-size:10.5px;line-height:17px;color:var(--muted)}
.features{display:flex;justify-content:center;gap:0;margin-top:38px}
.feature{width:220px;text-align:center}
.feature .ring{width:62px;height:62px;border-radius:50%;background:#d8ecc0;margin:0 auto;display:flex;align-items:center;justify-content:center}
.feature .ring.dark{background:var(--teal)}
.feature h3{font-size:11px;font-weight:700;margin-top:16px}
.feature p{font-size:9px;color:var(--muted);line-height:14px;margin-top:6px;width:150px;margin-left:auto;margin-right:auto}

.compound{height:322px;padding-top:32px}
.compound .wrap{display:flex;justify-content:space-between}
.compound .text{width:420px}
.compound h2{font-size:28px;font-weight:300;color:#41474d}
.compound .lead{font-size:10px;line-height:16px;color:var(--muted);margin-top:18px}
.ticks{list-style:none;margin-top:16px}
.ticks li{display:flex;gap:8px;align-items:center;font-size:10px;color:var(--muted);margin-bottom:9px}
.more{display:inline-block;margin-top:10px;border:1px solid #c7ccd1;padding:7px 14px;font-size:10px;color:#555}
.compound .photo{width:350px;height:212px;margin-top:4px;background:linear-gradient(135deg,#cfe3ec,#9fc3d4 55%,#e9eef1)}

.band{height:232px;background:repeating-linear-gradient(45deg,var(--band) 0 6px,var(--band-dark) 6px 7px);text-align:center;color:var(--white);padding-top:56px}
.band h2{font-size:25px;font-weight:300}
.band h2 span{color:var(--lime)}
.band p{font-size:10px;color:#aab3bb;margin-top:10px}
.band .btns{margin-top:22px;display:flex;justify-content:center;gap:12px}
.btn{display:inline-block;width:112px;height:28px;line-height:28px;font-size:9px;font-weight:700;letter-spacing:.5px}
.btn.green{background:var(--lime);color:var(--white)}
.btn.outline{border:1px solid #cfd5da;color:var(--white)}

.info{height:456px;padding-top:44px}
.info .wrap{display:flex;justify-content:space-between}
.col{width:250px}
.col h2{font-size:27px;font-weight:300;color:#4a5056;padding-bottom:14px;border-bottom:1px solid var(--line)}
.map{margin-top:18px;height:170px;background:linear-gradient(135deg,#eee6d4,#f3eee2 50%,#dfe7d8)}
.hours{width:100%;margin-top:16px;border-collapse:collapse;font-size:10px}
.hours td{padding:5px 0;color:var(--muted)}
.hours td:first-child{color:var(--ink);font-weight:700;width:90px}
.reach{list-style:none;margin-top:16px}
.reach li{display:flex;gap:10px;font-size:10px;color:var(--muted);margin-bottom:12px;align-items:flex-start;line-height:15px}
.socials{display:flex;gap:10px;margin-top:8px}
.socials span{width:16px;height:16px;background:#5b636b;border-radius:2px}

.footer{height:300px;background:var(--foot);padding-top:30px}
.footer .wrap{display:flex;justify-content:space-between}
.fcol{width:250px}
.fcol h4{font-size:11px;font-weight:900;letter-spacing:1px;color:#3a4046;margin-bottom:14px}
.fcol p{font-size:9px;line-height:15px;color:var(--muted)}
.news{display:flex;gap:10px;margin-bottom:16px}
.news .thumb{width:40px;height:40px;background:linear-gradient(135deg,#d6e1e7,#b8cbd6);flex:none}
.news b{font-size:10px;display:block;color:var(--ink)}
.news i{font-style:normal;font-size:8.5px;color:var(--muted)}
.field{height:24px;background:var(--white);border:1px solid #d8dcdf;margin-bottom:8px;font-size:9px;color:#a5abb1;padding:5px 8px}
.field.area{height:56px}
.send{width:100%;height:26px;background:#5aa9c2;color:var(--white);font-size:9px;font-weight:700;text-align:center;line-height:26px;letter-spacing:.5px}

.bottom{height:60px;background:var(--bottom);color:#8d959c;font-size:9px}
.bottom .wrap{display:flex;justify-content:space-between;align-items:center;height:60px}
.bottom .marks{display:flex;gap:6px}
.bottom .marks span{width:22px;height:12px;background:#4a5259;border-radius:2px}
</style>
</head>
<body>

<div class="topbar">
  <div class="wrap">
    <div class="left"><span>English</span><span class="select">Select Branch</span></div>
    <div class="right"><span class="sq"></span><span class="sq"></span><span class="sq"></span><span class="sq"></span></div>
  </div>
</div>

<header class="header">
  <div class="wrap">
    <div class="logo">COMPOUNDING PHARMACY</div>
    <nav class="nav"><a>Home</a><a>About us</a><a>Locations</a><a>Timings</a><a>Contact</a></nav>
  </div>
</header>

<section class="hero" role="img" aria-label="Smiling pharmacist in a white coat standing in front of bright pharmacy shelves">
  <div class="hero-title">Lorem ipsum dolor sit</div>
  <div class="hero-sub">Consectetur adipiscing</div>
  <div class="hero-btn">CONTACT NOW</div>
</section>

<section class="welcome">
  <h2 class="h-center">WELCOME</h2>
  <p class="intro">Lorem ipsum dolor sit amet, consectetur adipiscing elit. Vivamus lacinia odio vitae vestibulum vestibulum. Cras venenatis euismod malesuada. Nullam ac erat ante, in tincidunt purus. Sed at lorem in nunc porta tristique. Proin nec augue quisque aliquam tempor magna, pellentesque habitant morbi tristique senectus et netus et malesuada fames ac turpis egestas. Donec sed odio dui, maecenas faucibus mollis interdum. Integer posuere erat a ante venenatis dapibus posuere velit aliquet. Aenean lacinia bibendum nulla sed consectetur. Curabitur blandit tempus porttitor, nullam quis risus eget urna mollis ornare vel eu leo. Vestibulum id ligula porta felis euismod semper, cum sociis natoque penatibus et magnis dis parturient montes.</p>
  <div class="features">
    <div class="feature">
      <div class="ring"><svg width="26" height="26" viewBox="0 0 24 24" fill="none" stroke="#5e8f2a" stroke-width="2"><circle cx="12" cy="12" r="8"/><path d="M12 8v4l3 2"/></svg></div>
      <h3>Lorem Ipsum</h3><p>Nulla vitae elit libero, a pharetra augue mollis.</p>
    </div>
    <div class="feature">
      <div class="ring"><svg width="26" height="26" viewBox="0 0 24 24" fill="none" stroke="#5e8f2a" stroke-width="2"><path d="M5 12l4 4 10-10"/></svg></div>
      <h3>Excellent Quality</h3><p>Donec ullamcorper nulla non metus auctor fringilla.</p>
    </div>
    <div class="feature">
      <div class="ring dark"><svg width="26" height="26" viewBox="0 0 24 24" fill="none" stroke="#ffffff" stroke-width="2"><path d="M4 9h16l-2 10H6z"/><path d="M9 9V6a3 3 0 0 1 6 0v3"/></svg></div>
      <h3>Super Online Store</h3><p>Etiam porta sem malesuada magna mollis euismod.</p>
    </div>
    <div class="feature">
      <div class="ring"><svg width="26" height="26" viewBox="0 0 24 24" fill="none" stroke="#5e8f2a" stroke-width="2"><path d="M5 4h4l2 5-2 1a11 11 0 0 0 5 5l1-2 5 2v4a2 2 0 0 1-2 2A16 16 0 0 1 3 6a2 2 0 0 1 2-2z"/></svg></div>
      <h3>24/7 Support</h3><p>Cras mattis consectetur purus sit amet fermentum.</p>
    </div>
  </div>
</section>

<section class="compound">
  <div class="wrap">
    <div class="text">
      <h2>We do Compounding</h2>
      <p class="lead">Fusce dapibus, tellus ac cursus commodo, tortor mauris condimentum nibh, ut fermentum massa justo sit amet risus. Maecenas sed diam eget risus varius blandit sit amet non magna.</p>
      <ul class="ticks">
        <li><svg width="10" height="10" viewBox="0 0 10 10"><path d="M1 5l3 3 5-6" stroke="#8cc63f" stroke-width="1.6" fill="none"/></svg>Tailored medicines prepared in our own laboratory</li>
        <li><svg width="10" height="10" viewBox="0 0 10 10"><path d="M1 5l3 3 5-6" stroke="#8cc63f" stroke-width="1.6" fill="none"/></svg>Formulations for patients, prescribers and vets</li>
        <li><svg width="10" height="10" viewBox="0 0 10 10"><path d="M1 5l3 3 5-6" stroke="#8cc63f" stroke-width="1.6" fill="none"/></svg>Friendly advice from experienced pharmacists</li>
      </ul>
      <span class="more">Read more</span>
    </div>
    <div class="photo" role="img" aria-label="Gloved hands preparing a compounded medicine at a laboratory bench"></div>
  </div>
</section>

<section class="band">
  <h2>Lorem ipsum dolor sit amet, <span>consectetur adipiscing</span> elit. Vivamus lacinia</h2>
  <p>Praesent commodo cursus magna, vel scelerisque nisl consectetur et. Nullam id dolor id nibh ultricies vehicula ut id elit.</p>
  <div class="btns"><span class="btn green">GET IN TOUCH</span><span class="btn outline">READ MORE</span></div>
</section>

<section class="info">
  <div class="wrap">
    <div class="col">
      <h2>Where we are</h2>
      <div class="map" role="img" aria-label="Street map showing the pharmacy location"></div>
    </div>
    <div class="col">
      <h2>Our timings</h2>
      <table class="hours">
        <tr><td>Monday</td><td>9am to 6pm</td></tr>
        <tr><td>Tuesday</td><td>9am to 6pm</td></tr>
        <tr><td>Wednesday</td><td>9am to 6pm</td></tr>
        <tr><td>Thursday</td><td>9am to 8pm</td></tr>
        <tr><td>Friday</td><td>9am to 6pm</td></tr>
        <tr><td>Saturday</td><td>9am to 1pm</td></tr>
        <tr><td>Sunday</td><td>Closed</td></tr>
      </table>
    </div>
    <div class="col">
      <h2>How to reach us</h2>
      <ul class="reach">
        <li><svg width="12" height="12" viewBox="0 0 24 24" fill="none" stroke="#5b636b" stroke-width="2"><rect x="3" y="5" width="18" height="14"/><path d="M3 6l9 7 9-7"/></svg>hello@compoundingpharmacy.example</li>
        <li><svg width="12" height="12" viewBox="0 0 24 24" fill="none" stroke="#5b636b" stroke-width="2"><path d="M5 4h4l2 5-2 1a11 11 0 0 0 5 5l1-2 5 2v4a2 2 0 0 1-2 2A16 16 0 0 1 3 6a2 2 0 0 1 2-2z"/></svg>+1 (555) 014 2290<br>+1 (555) 014 2291</li>
        <li><svg width="12" height="12" viewBox="0 0 24 24" fill="none" stroke="#5b636b" stroke-width="2"><path d="M12 22s7-7 7-12a7 7 0 0 0-14 0c0 5 7 12 7 12z"/><circle cx="12" cy="10" r="2.5"/></svg>48 Harbour Lane, Suite 12<br>Riverton 4021</li>
      </ul>
      <div class="socials"><span></span><span></span><span></span><span></span><span></span><span></span></div>
    </div>
  </div>
</section>

<footer class="footer">
  <div class="wrap">
    <div class="fcol">
      <h4>ABOUT US</h4>
      <p>Maecenas sed diam eget risus varius blandit sit amet non magna. Donec id elit non mi porta gravida at eget metus. Cum sociis natoque penatibus et magnis dis parturient montes, nascetur ridiculus mus. Etiam porta sem malesuada magna mollis euismod. Aenean eu leo quam, pellentesque ornare sem lacinia quam venenatis vestibulum.</p>
    </div>
    <div class="fcol">
      <h4>LATEST NEWS</h4>
      <div class="news"><div class="thumb" role="img" aria-label="News photo"></div><div><b>New This Blog Here</b><i>Vivamus sagittis lacus vel augue laoreet.</i></div></div>
      <div class="news"><div class="thumb" role="img" aria-label="News photo"></div><div><b>New This Blog Here</b><i>Nullam quis risus eget urna mollis ornare.</i></div></div>
    </div>
    <div class="fcol">
      <h4>QUICK CONTACT US</h4>
      <div class="field">Name</div>
      <div class="field">Email</div>
      <div class="field area">Message</div>
      <div class="send">SEND TO US</div>
    </div>
  </div>
</footer>

<div class="bottom">
  <div class="wrap">
    <span>Copyright 2024 Compounding Pharmacy. All rights reserved.</span>
    <div class="marks"><span></span><span></span><span></span></div>
  </div>
</div>

</body>
</html>
```